Brightfen Business Card Redesign & Logo Update

We need to update our business cards to something more modern and fresh. Brightfen can provide the current color schemes and old design examples, but welcome creativity in helping us with this redesign. PLEASE NOTE that we no longer utilize the "tree" and/or "leaf" imagery in our branding. If able would apprecaite an update on the quality of our "words only" logo in Ai. / PNG formats too.

Target Market(s)

Investors, landowners, corporate partners, contractors

Industry/Entity Type

Environmental Restoration & Conservation

Contact Information for Business Card

Logo, persons name, title, mailing address, phone and email, website url

Font styles to use
Other font styles liked:
• Merriweather

Requirements
Nice to have
• Logo, persons name, title, mailing address, phone and email, website url, but open to ideams
Should not have
• No all back backgrounds

```html
<!DOCTYPE html>
<html lang="en">
<head>
<meta charset="UTF-8">
<title>Brightfen Business Card</title>
<link href="https://fonts.googleapis.com/css2?family=Montserrat:wght@500;700;800&display=swap" rel="stylesheet">
<style>
  :root {
    --brand-green: #177c3f;
    --brand-orange: #ee7f22;
    --ink: #1c1c1c;
    --paper: #ffffff;
    --backdrop: #d9d9d9;
  }
  * { margin: 0; padding: 0; box-sizing: border-box; }
  html, body {
    width: 1200px; height: 856px; overflow: hidden;
    background: var(--backdrop);
    font-family: "Montserrat", Arial, sans-serif;
  }
  .sheet {
    width: 1200px; height: 856px;
    display: flex; align-items: center; justify-content: center; gap: 48px;
  }
  .card {
    position: relative;
    width: 540px; height: 309px;
    border-bottom: 4px solid var(--brand-orange);
    border-right: 2px solid var(--brand-orange);
    box-shadow: 0 10px 24px rgba(0,0,0,0.25);
  }
  .card--front { background: var(--paper); }
  .card--back { background: var(--brand-green); }

  .wordmark {
    font-weight: 800; letter-spacing: 1px; line-height: 1;
    text-transform: uppercase;
  }
  .tagline {
    font-weight: 700; font-size: 10.5px; letter-spacing: 1.2px;
    text-transform: uppercase; color: var(--ink); margin-top: 4px;
  }
  .card--front .brand {
    position: absolute; top: 36px; right: 40px; text-align: right;
  }
  .card--front .wordmark { font-size: 40px; color: var(--brand-orange); }

  .card--back .brand {
    position: absolute; left: 0; right: 0; top: 50%;
    transform: translateY(-50%); text-align: center;
  }
  .card--back .wordmark { font-size: 68px; color: var(--brand-orange); }
  .card--back .tagline { font-size: 17px; letter-spacing: 2.5px; margin-top: 8px; }

  .address {
    position: absolute; right: 40px; top: 150px; text-align: right;
    font-size: 12px; font-weight: 500; line-height: 1.5; color: var(--ink);
  }
  .person { position: absolute; left: 36px; top: 120px; }
  .person__name {
    font-size: 17px; font-weight: 800; letter-spacing: 0.5px;
    color: var(--brand-orange);
  }
  .person__name .first { color: var(--brand-green); }
  .person__title { font-size: 12px; font-weight: 500; color: var(--ink); margin-top: 2px; }

  .contacts {
    position: absolute; left: 36px; bottom: 28px; list-style: none;
  }
  .contacts li {
    display: flex; align-items: center; gap: 10px;
    font-size: 12.5px; font-weight: 500; color: var(--ink);
    margin-top: 6px;
  }
  .contacts svg { width: 20px; height: 20px; flex: none; }
</style>
</head>
<body>
<main class="sheet">
  <section class="card card--front">
    <div class="brand">
      <div class="wordmark">Brightfen</div>
      <div class="tagline">Environmental Credit Company</div>
    </div>
    <address class="address">
      42-07 Linden Ave 14<br>Fairport, NY 14450
    </address>
    <div class="person">
      <div class="person__name"><span class="first">Dale</span> Harrow</div>
      <div class="person__title">Managing Director</div>
    </div>
    <ul class="contacts">
      <li>
        <svg viewBox="0 0 20 20" aria-hidden="true"><circle cx="10" cy="10" r="10" fill="#ee7f22"/><path d="M7 5.5l1.6 0 .8 2.3-1.1.8a6 6 0 0 0 3.1 3.1l.8-1.1 2.3.8v1.6c0 .6-.5 1-1 1A8 8 0 0 1 6 6.5c0-.5.4-1 1-1z" fill="#fff"/></svg>
        555-204-3176
      </li>
      <li>
        <svg viewBox="0 0 20 20" aria-hidden="true"><circle cx="10" cy="10" r="10" fill="#ee7f22"/><rect x="5" y="6.5" width="10" height="7" fill="none" stroke="#fff" stroke-width="1.3"/><path d="M5 6.5l5 4 5-4" fill="none" stroke="#fff" stroke-width="1.3"/></svg>
        info@brightfen.com
      </li>
      <li>
        <svg viewBox="0 0 20 20" aria-hidden="true"><circle cx="10" cy="10" r="10" fill="#ee7f22"/><circle cx="10" cy="10" r="5" fill="none" stroke="#fff" stroke-width="1.2"/><ellipse cx="10" cy="10" rx="2.2" ry="5" fill="none" stroke="#fff" stroke-width="1.2"/><path d="M5 10h10" stroke="#fff" stroke-width="1.2"/></svg>
        www.brightfen.com
      </li>
    </ul>
  </section>

  <section class="card card--back">
    <div class="brand">
      <div class="wordmark">Brightfen</div>
      <div class="tagline">Environmental Credit Company</div>
    </div>
  </section>
</main>
</body>
</html>
```